Online Shop - Website Design for up an coming art studio

We require a fully functional website design - not just design - but complete coded online shop website please, which should be a word press style frame work to allow ease up updating the site in the future. The website will sell art work from up and coming artists. The business is called "Brindle Harbor Studios". I have attached our logo to allow the submitted designs to tie in with this.

Industry/Entity Type

Shop

Coding

Coded - Design and coding required

Number of Pages Required

1 page

Colors

Designer to choose colors to be used in the design.

Requirements
Must have
• The website design must incorporate and fully functional online eCommerce shop feature.

```html
<!DOCTYPE html>
<html lang="en">
<head>
<meta charset="utf-8">
<title>Brindle Harbor Studios</title>
<link href="https://fonts.googleapis.com/css2?family=Jost:wght@400;500;600&family=Open+Sans:ital,wght@0,400;0,600;0,700;1,600&display=swap" rel="stylesheet">
<style>
:root{
  --red:#e31b47;
  --blue:#1ea7e1;
  --green:#9ccc3c;
  --orange:#f7941d;
  --dark:#333333;
  --text:#555555;
  --muted:#777777;
  --light:#f4f4f4;
  --line:#e3e3e3;
  --white:#ffffff;
}
*{margin:0;padding:0;box-sizing:border-box}
html,body{width:1200px;height:2550px;overflow:hidden;background:var(--white)}
body{font-family:"Open Sans",sans-serif;color:var(--text);position:relative}
.abs{position:absolute}
.heading{font-family:"Jost",sans-serif;color:var(--dark);text-transform:uppercase}

/* header */
.brand{left:110px;top:22px;width:220px;text-align:center}
.brand-dot{width:74px;height:74px;border-radius:50%;background:var(--dark);margin:0 auto 6px}
.brand-name{font-family:"Jost",sans-serif;font-size:19px;font-weight:500;color:var(--dark);letter-spacing:1px;text-transform:uppercase}
.address{left:617px;top:22px;width:300px;font-size:11.5px;line-height:21px;color:var(--text);padding-left:34px}
.address b{color:var(--dark);font-size:11px}
.address svg{position:absolute;left:0;top:2px}
.divider{left:912px;top:24px;width:1px;height:56px;background:var(--line)}
.cart{left:930px;top:28px;display:flex;align-items:center;gap:8px;font-size:11px;font-weight:700;color:var(--dark)}
.cart-icon{width:46px;height:46px;border:1px solid var(--blue);border-radius:50%;display:flex;align-items:center;justify-content:center}
.cart span{color:var(--blue)}
.nav{left:434px;top:106px;display:flex;gap:0;font-family:"Jost",sans-serif;font-size:13px;font-weight:500;color:var(--dark)}
.nav a{text-decoration:none;color:inherit;position:absolute;white-space:nowrap}
.nav a.active{color:var(--red)}
.search{left:1052px;top:104px}

/* hero */
.hero{left:0;top:148px;width:1200px;height:507px;background:linear-gradient(100deg,#c9c4bc 0%,#e8e3dc 35%,#d8d6d2 60%,#f1f1f1 100%)}
.hero-bar{left:0;top:650px;width:1200px;height:5px;display:flex}
.hero-bar i{flex:1}
.hero-title{left:536px;top:296px;width:532px;height:78px;background:rgba(51,51,51,.85);color:var(--white);font-family:"Jost",sans-serif;font-size:56px;line-height:78px;padding-left:24px;letter-spacing:1px}
.hero-text{left:536px;top:374px;width:532px;height:82px;background:rgba(51,51,51,.75);color:var(--white);font-size:13px;line-height:22px;padding:14px 24px 0 52px}
.btn{background:var(--orange);color:var(--white);border-radius:22px;font-family:"Jost",sans-serif;font-size:12.5px;font-weight:500;text-transform:uppercase;text-align:center}
.hero-btn{left:918px;top:462px;width:150px;height:43px;line-height:43px}
.slide-arrow{top:570px;width:34px;height:34px;border-radius:50%;background:rgba(40,40,40,.7);display:flex;align-items:center;justify-content:center}

/* service grid */
.grid{left:133px;top:687px;width:935px;height:455px;display:grid;grid-template-columns:repeat(3,1fr);grid-template-rows:repeat(2,1fr)}
.tile{color:var(--white);text-align:center;padding:32px 28px 0}
.tile-icon{width:74px;height:74px;border:2px solid var(--white);border-radius:50%;margin:0 auto 20px;display:flex;align-items:center;justify-content:center}
.tile h3{font-family:"Jost",sans-serif;font-size:13px;font-weight:600;margin-bottom:8px}
.tile p{font-size:11px;line-height:20px}
.tile.red{background:var(--red)}
.tile.blue{background:var(--blue)}
.tile.green{background:var(--green)}
.photo-a{background:linear-gradient(135deg,#4a3a30,#8a7460 55%,#2e2620)}
.photo-b{background:linear-gradient(135deg,#6e7a64,#b0b2aa 50%,#5a5e56)}
.photo-c{background:linear-gradient(135deg,#8e8a86,#c9c5bf 50%,#6e6a66)}

/* welcome */
.welcome{left:0;top:1187px;width:1200px;height:306px;background:linear-gradient(90deg,#f0f0f0 0%,#f0f0f0 45%,#e6e1da 70%,#d8cbb8 100%)}
.welcome-title{left:133px;top:1233px;font-size:27px;line-height:32px;font-weight:400;letter-spacing:.5px}
.welcome-text{left:133px;top:1304px;width:470px;font-size:11px;line-height:22px;color:var(--text)}
.welcome-btn{left:133px;top:1389px;width:150px;height:43px;line-height:43px}

/* artwork */
.section-title{left:0;top:1553px;width:1200px;text-align:center;font-size:26px}
.section-sub{left:0;top:1590px;width:1200px;text-align:center;font-size:12px;color:var(--text)}
.pager{top:1556px;width:26px;height:26px;border:1px solid #cfcfcf;display:flex;align-items:center;justify-content:center}
.cards{left:133px;top:1640px;width:935px;display:flex;justify-content:space-between}
.card{width:218px;height:369px;border:1px solid var(--line);box-shadow:0 1px 5px rgba(0,0,0,.12);text-align:center;padding-top:22px}
.card-art{width:176px;height:176px;border-radius:50%;margin:0 auto;border:8px solid var(--dark);outline:2px dashed #bbb;outline-offset:-12px}
.card h4{font-family:"Jost",sans-serif;font-size:12.5px;font-weight:500;color:var(--dark);margin:24px 0 6px}
.card p{font-size:11px;line-height:18px;color:var(--text)}
.price{font-size:17px;font-weight:600;color:var(--red);margin:12px 0 10px}
.card .btn{width:98px;height:36px;line-height:36px;margin:0 auto}

/* testimonial */
.testimonial{left:0;top:2079px;width:1200px;height:145px;background:var(--red)}
.avatar{left:133px;top:2110px;width:84px;height:84px;border-radius:50%;border:3px solid var(--white);background:linear-gradient(#e8dcd0,#b9a48f)}
.quote-rule{left:250px;top:2108px;width:1px;height:88px;background:rgba(255,255,255,.5)}
.quote{left:285px;top:2112px;width:785px;color:var(--white);font-size:13px;font-style:italic;font-weight:600;line-height:22px}
.quote-by{left:285px;top:2166px;color:var(--white);font-size:12px}

/* footer */
.footer{left:0;top:2224px;width:1200px;height:255px;background:var(--light)}
.foot-brand{left:133px;top:2268px;width:170px;text-align:center}
.foot-brand .brand-dot{width:72px;height:72px}
.foot-brand .brand-name{font-size:17px}
.social{display:flex;justify-content:center;gap:5px;margin-top:12px}
.social i{width:22px;height:22px;border-radius:50%;border:1px solid #7b8ba0;display:block}
.foot-col{top:2266px;font-size:11px;line-height:22.5px;color:var(--text)}
.foot-col h5{font-family:"Jost",sans-serif;font-size:14px;font-weight:500;color:var(--dark);margin-bottom:6px;text-transform:uppercase}
.foot-col.links a{text-decoration:underline;color:var(--text);display:block}
.foot-col div{display:block}
.email{width:208px;height:34px;border:1px solid var(--line);border-radius:18px;background:var(--white);font-size:10px;line-height:32px;padding-left:16px;color:#aaa;margin-top:6px}
.subscribe{width:110px;height:34px;line-height:34px;margin-top:12px}
.copyright{left:133px;top:2508px;font-size:10.5px;color:var(--text)}
.payment{left:784px;top:2500px;display:flex;align-items:center;gap:6px;font-size:10.5px;color:var(--text)}
.payment span{margin-right:10px}
.payment i{width:34px;height:23px;display:block;border-radius:2px}
</style>
</head>
<body>

<!-- header -->
<div class="abs brand">
  <div class="brand-dot"></div>
  <div class="brand-name">Brindle Harbor Studios</div>
</div>

<div class="abs address">
  <svg width="20" height="28" viewBox="0 0 20 28"><path d="M10 0C4.5 0 0 4.4 0 9.8 0 17 10 28 10 28s10-11 10-18.2C20 4.4 15.5 0 10 0z" fill="#f7941d"/><circle cx="10" cy="9.5" r="3.5" fill="#fff"/></svg>
  <b>ADDRESS :</b><br>42 Larkfield Lane, Millbrook, Eastshire,<br>Scotland, KB7 4QN
</div>
<div class="abs divider"></div>
<div class="abs cart">
  <div class="cart-icon">
    <svg width="24" height="22" viewBox="0 0 24 22" fill="none" stroke="#1ea7e1" stroke-width="1.6"><path d="M1 2h4l3 12h12l3-9H6.5"/><circle cx="10" cy="19" r="1.6"/><circle cx="18" cy="19" r="1.6"/></svg>
  </div>
  MY CART IS : <span>(0)</span>
</div>

<nav class="abs nav">
  <a class="active" style="left:0">HOME</a>
  <a style="left:69px">ABOUT US</a>
  <a style="left:161px">SERVICES</a>
  <a style="left:246px">ARTWORK</a>
  <a style="left:334px">TESTIMONIALS</a>
  <a style="left:450px">BLOG</a>
  <a style="left:515px">CONTACT US</a>
</nav>
<svg class="abs search" width="18" height="18" viewBox="0 0 18 18" fill="none" stroke="#f7941d" stroke-width="2"><circle cx="7.5" cy="7.5" r="5.5"/><path d="M11.5 11.5l5 5"/></svg>

<!-- hero -->
<div class="abs hero" role="img" aria-label="Photo of two artists working at a digital drawing studio desk"></div>
<div class="abs hero-bar"><i style="background:var(--blue)"></i><i style="background:var(--red)"></i><i style="background:var(--green)"></i><i style="background:#f4d21f"></i><i style="background:var(--blue)"></i><i style="background:var(--red)"></i></div>
<div class="abs hero-title">ARTWORK STUDIO</div>
<div class="abs hero-text">Lorem ipsum dolor sit amet, consectetur adipiscing elit, sed do eiusmod tempor incididunt ut labore et dolore magna aliqua.</div>
<div class="abs btn hero-btn">Learn More Info</div>
<div class="abs slide-arrow" style="left:131px"><svg width="10" height="12" viewBox="0 0 10 12"><path d="M7 1L2 6l5 5" fill="none" stroke="#fff" stroke-width="2"/></svg></div>
<div class="abs slide-arrow" style="left:171px"><svg width="10" height="12" viewBox="0 0 10 12"><path d="M3 1l5 5-5 5" fill="none" stroke="#fff" stroke-width="2"/></svg></div>

<!-- service grid -->
<section class="abs grid">
  <div class="tile red">
    <div class="tile-icon"><svg width="36" height="36" viewBox="0 0 36 36" fill="none" stroke="#fff" stroke-width="2"><path d="M18 4C9 4 3 10 3 18s6 14 14 14c3 0 3-3 1.5-4.5S18 23 21 23h5c4 0 7-3 7-7C33 9 26 4 18 4z"/><circle cx="11" cy="15" r="2"/><circle cx="17" cy="10" r="2"/><circle cx="24" cy="12" r="2"/></svg></div>
    <h3>TEMPOR INCIDIDUNT</h3>
    <p>Lorem ipsum dolor sit amet, consectetur adipiscing elit, sed do eiusmod tempor incididunt ut labore dolore magn cupidatat...</p>
  </div>
  <div class="photo-a" role="img" aria-label="Photo of paint brushes in jars on a workbench"></div>
  <div class="tile blue">
    <div class="tile-icon"><svg width="36" height="34" viewBox="0 0 36 34" fill="none" stroke="#fff" stroke-width="2"><rect x="3" y="4" width="30" height="20" rx="1"/><path d="M13 30h10M18 24v6M12 19l10-10 3 3-10 10h-3z"/></svg></div>
    <h3>TEMPOR INCIDIDUNT</h3>
    <p>Lorem ipsum dolor sit amet, consectetur adipiscing elit, sed do eiusmod tempor incididunt ut labore dolore magn cupidatat...</p>
  </div>
  <div class="photo-b" role="img" aria-label="Photo of a designer typing on a laptop with design software open"></div>
  <div class="tile green">
    <div class="tile-icon"><svg width="36" height="34" viewBox="0 0 36 34" fill="none" stroke="#fff" stroke-width="2"><rect x="7" y="3" width="26" height="22"/><path d="M3 9v22h24"/><path d="M10 22l7-8 5 5 3-3 5 6"/><circle cx="26" cy="9" r="2"/></svg></div>
    <h3>TEMPOR INCIDIDUNT</h3>
    <p>Lorem ipsum dolor sit amet, consectetur adipiscing elit, sed do eiusmod tempor incididunt ut labore dolore magn cupidatat...</p>
  </div>
  <div class="photo-c" role="img" aria-label="Photo of an architect working on a model at a studio table"></div>
</section>

<!-- welcome -->
<div class="abs welcome" role="img" aria-label="Photo of paint brushes, palette and easel on a bright studio table"></div>
<h2 class="abs heading welcome-title">Welcome to<br>Brindle Harbor Studios</h2>
<p class="abs welcome-text">Commodo consequat. Duis aute irure dolor in reprehenderit in voluptate velit esse cillum dolore eu fugiat nulla pariatur. Excepteur sint occaecat cupidatat non proident, sunt in culpa qui officia sequi nesciunt...</p>
<div class="abs btn welcome-btn">Learn More Info</div>

<!-- artwork -->
<h2 class="abs heading section-title">Artwork</h2>
<p class="abs section-sub">Lorem ipsum dolor sit amet, consectetur adipiscing elit, sed do eiusmod tempor incididunt</p>
<div class="abs pager" style="left:1008px"><svg width="8" height="10" viewBox="0 0 8 10"><path d="M6 1L2 5l4 4" fill="none" stroke="#555" stroke-width="1.5"/></svg></div>
<div class="abs pager" style="left:1040px"><svg width="8" height="10" viewBox="0 0 8 10"><path d="M2 1l4 4-4 4" fill="none" stroke="#555" stroke-width="1.5"/></svg></div>

<section class="abs cards">
  <article class="card">
    <div class="card-art" role="img" aria-label="Painting of a street scene with red umbrellas" style="background:linear-gradient(135deg,#9a9a9a,#d33 50%,#555)"></div>
    <h4>EXCEPTEUR SINT</h4>
    <p>Aliquip ex ea commodo consequat.<br>Duis aute irure dolor...</p>
    <div class="price">$44.00</div>
    <div class="btn">Buy Now</div>
  </article>
  <article class="card">
    <div class="card-art" role="img" aria-label="Painting of a bicycle with flower baskets" style="background:linear-gradient(135deg,#b6a7c9,#8c9a6a 50%,#d8cfc0)"></div>
    <h4>EXCEPTEUR SINT</h4>
    <p>Aliquip ex ea commodo consequat.<br>Duis aute irure dolor...</p>
    <div class="price">$36.00</div>
    <div class="btn">Buy Now</div>
  </article>
  <article class="card">
    <div class="card-art" role="img" aria-label="Painting of an autumn city street in warm tones" style="background:linear-gradient(135deg,#8a7a55,#d9c79a 50%,#6b5e44)"></div>
    <h4>EXCEPTEUR SINT</h4>
    <p>Aliquip ex ea commodo consequat.<br>Duis aute irure dolor...</p>
    <div class="price">$52.00</div>
    <div class="btn">Buy Now</div>
  </article>
  <article class="card">
    <div class="card-art" role="img" aria-label="Painting of a city avenue with yellow taxis" style="background:linear-gradient(135deg,#6d6d6d,#c8c8c8 50%,#d6b03a)"></div>
    <h4>EXCEPTEUR SINT</h4>
    <p>Aliquip ex ea commodo consequat.<br>Duis aute irure dolor...</p>
    <div class="price">$47.00</div>
    <div class="btn">Buy Now</div>
  </article>
</section>

<!-- testimonial -->
<div class="abs testimonial"></div>
<div class="abs avatar" role="img" aria-label="Customer portrait"></div>
<div class="abs quote-rule"></div>
<p class="abs quote">“Lorem ipsum dolor sit amet, consectetur adipiscing elit, sed do eiusmod tempor incididunt ut labore et dolore magna aliqua. Ut enim ad minim veniam, quis nostrud exercitation ullamco laboris nisi ut aliquip ex ea commodo....</p>
<div class="abs quote-by">-JOHN DOE &nbsp;&nbsp;★★★★☆</div>

<!-- footer -->
<div class="abs footer"></div>
<div class="abs foot-brand">
  <div class="brand-dot"></div>
  <div class="brand-name">Brindle Harbor Studios</div>
  <div class="social"><i></i><i></i><i></i><i></i></div>
</div>
<div class="abs foot-col links" style="left:375px">
  <h5>Quick Links</h5>
  <a>Contact</a><a>FAQ</a><a>Delivery</a><a>Returns</a><a>Track Orders</a><a>Subscribe</a>
</div>
<div class="abs foot-col" style="left:534px">
  <h5>My Account</h5>
  <div>Delivery Information</div><div>Privacy Policy</div><div>Returns Policy</div><div>Terms and Conditions</div><div>FAQs</div>
</div>
<div class="abs foot-col" style="left:717px">
  <h5>Extras</h5>
  <div>Specials</div><div>New products</div><div>Top sellers</div><div>Our stores</div><div>Contact us</div><div>About us</div>
</div>
<div class="abs foot-col" style="left:860px">
  <h5>Newsletter</h5>
  <div class="email">Enter Email Address</div>
  <div class="btn subscribe">Subscribe</div>
</div>

<div class="abs copyright">Copyrights © Brindle Harbor Studios , 2017 | All rights Reserved.</div>
<div class="abs payment">
  <span>Payment Info :</span>
  <i style="background:#2a5aa8"></i><i style="background:#e5e5e5"></i><i style="background:#3a8fd6"></i><i style="background:#d9d9d9"></i><i style="background:#1e4e9a"></i>
</div>

</body>
</html>
```